Boutique startup consulting

Hello,
Me and my partner are starting a boutique consulting/ "venturing for startup" firm and want to make professional looking slides. The point of these slide are to attract Automakers's venture arms to collaborate with us. We are hoping to win clients with this presentation.

Acceptance criteria:
1. You put beautiful designs where-ever you can and make the attached slides look professional. Full freedom in designing the slides. You are the artist, please create some magic
2. The style should be innovative and state of the art. It should be with colourful designs
3. The slides should be very professional
4. We are unsure of how to present our previous experience. Please help us out
5. The first slide has gray background. you may use the original colored image and tweak it

Here is out website:
https://www.talvora-partners.net/

Can you please ensure that the slides are presented in the following format?

PRESENTATION
1. Starting Masterslide
2. Customized Starting Masterslide (with Topic + Customer Logo, for eg. Smart City & KDR)
3. Service Categories Masterslide /Overview ( we have 5 Categories which are shown by icon and buzzword, see https://www.talvora-partners.net/live/research-strategy/research-strategy.aspx, this is for eg. the Overview for the categorie “Research &Strategy”. We have 2-4 Icon per Category, other categories are Business Development,Venture Building, Expansion Advisory, Sustainable Due Diligence , see webside)
4. Subcategories & Description Masterslide
o We have 15 Subcategories, the Masterslide should just show the Icon and then 1-2 square for description with bullets, f.ex. https://www.talvora-partners.net/live/expansion-advisory-feasibility-analysis/feasibility-analysis.aspx
5. Team Presenting Masterslide
o Not like Website, a Masterslide where each Teammember can present him self, in bullets with Education/Business Experience/ other awards/distinction AND in Text bubbles like “Experiences and hands-on Business developer”
6. Contact ( closing Chart with contact data, liked in etc.)
7. Masterslide (free for individual content)
o Just a slide with the CI framework which can be used as Masterslide for other charts like

8. PROPOSAL Masterslide (like customized starting slide, but Proposal)
9. Background Masterslide (Text)
o A textual description
10. Value Proposition & Goals Masterslide (Text & Bullets)
o V P will be textual so for eg. text frame; Goals with 2-4 squares (text/Bullets) for sub-goals and including the tasks for these goals in bullets
11. Milestones & Timing Masterslide (Timeline , Squares & text)
o Timeline, for eg. 6 Month project, where we have 8 tasks with starting and ending
12. Free MAsterslide /Proposal
o Where we can add charts to the proposal like Conditions or Contact

To Add:
- Logo colour description
- Picture and Icons ( so they don’t need to buy new pics or look for them)

Requirements
Must have
• Please check out the slides and make them presentable

```html
<!DOCTYPE html>
<html lang="en">
<head>
<meta charset="utf-8">
<title>Team – Corvin Delastre</title>
<link href="https://fonts.googleapis.com/css2?family=Hind:wght@400;500;600;700&family=Signika:wght@400;600&display=swap" rel="stylesheet">
<style>
:root{
  --green:#8cc63f;
  --light:#ededed;
  --black:#1b1b1b;
  --text:#2b2b2b;
  --muted:#555;
  --grey-circle:#cfcfcf;
  --white:#fff;
}
*{box-sizing:border-box;margin:0;padding:0}
html,body{width:1200px;height:675px;overflow:hidden;background:#fff}
.slide{position:relative;width:1200px;height:675px;overflow:hidden;font-family:"Hind",sans-serif;color:var(--text)}
.abs{position:absolute}

.profile-panel{left:0;top:0;width:662px;height:337px;background:var(--light)}
.stage-backdrop{left:0;top:337px;width:662px;height:338px;background:linear-gradient(160deg,#6b6b6b 0%,#575757 55%,#4a4a4a 100%)}
.portrait{left:0;top:50px;width:280px;height:260px;background:linear-gradient(135deg,#6e5a45 0%,#3a4256 50%,#7c8aa0 100%)}
.divider{left:323px;top:50px;width:3px;height:541px;background:var(--green)}
.icon-pill{left:308px;top:159px;width:31px;height:120px;background:var(--green);border-radius:4px}
.icon-pill svg{position:absolute;left:7px;width:17px;height:17px}

.name{left:360px;top:74px;font-family:"Signika",sans-serif;font-size:27px;color:var(--green);font-weight:400;white-space:nowrap}
.name b{font-weight:600}
.role{left:361px;top:112px;font-size:12.5px;letter-spacing:1.3px;color:var(--muted);white-space:nowrap}
.contact{left:360px;top:167px;font-size:14px;line-height:1.05;color:var(--text)}
.contact p{white-space:nowrap}
.contact .addr{margin-bottom:9px}
.contact .line{margin-bottom:8px}

.col-head{font-family:"Signika",sans-serif;font-size:16px;font-weight:600;color:var(--white);letter-spacing:.4px;padding-bottom:3px;border-bottom:2px solid var(--white)}
.honorary{left:62px;top:372px;width:218px}
.speaker{left:360px;top:372px;width:218px}
.entry{position:absolute;left:0;width:218px;color:var(--white)}
.entry .txt{font-size:12px;line-height:1.35;width:134px;white-space:nowrap}
.entry .date{font-size:9px;font-weight:700;letter-spacing:.3px;margin-top:2px}
.entry .badge{position:absolute;right:0;top:0;width:81px;height:40px;display:flex;align-items:center;justify-content:center;font-size:11px;font-weight:600;text-align:center;line-height:1.1}
.entry.sep{border-top:1px solid rgba(255,255,255,.55)}
.badge.navy{background:#0d3a5f;color:var(--white);font-size:14px}
.badge.white{background:var(--white);color:#333}
.badge.grey{background:#c8c8c8}
.badge.magenta{background:#c8236f;color:var(--white)}
.seal{width:30px;height:30px;border-radius:50%;background:#2d3d7a}

.crumb{left:0;top:632px;width:590px;height:27px;background:#3c3c3c;display:flex;align-items:center}
.crumb .num{width:60px;height:27px;background:var(--green);color:var(--white);font-weight:700;font-size:17px;display:flex;align-items:center;justify-content:center}
.crumb .path{margin-left:12px;font-size:15px;color:var(--white);letter-spacing:.4px;white-space:nowrap;padding-top:2px}
.crumb .path b{font-weight:700}
.crumb .path .hl{color:var(--green);font-weight:700}

.rail{left:662px;top:0;width:116px;height:675px;background:var(--black)}
.projects-band{left:662px;top:50px;width:538px;height:32px;background:var(--green)}
.projects-band span{position:absolute;left:155px;top:5px;font-family:"Signika",sans-serif;font-weight:600;font-size:19px;color:var(--white);letter-spacing:.5px}
.timeline-line{left:721px;top:134px;width:2px;height:389px;background:var(--white)}
.node{position:absolute;left:696px;width:52px;height:52px;border-radius:50%;background:var(--white);border:2px solid #bbb;display:flex;align-items:center;justify-content:center;text-align:center;font-size:8.5px;font-weight:600;line-height:1.05;color:#333}
.node.empty{background:var(--grey-circle);border-color:var(--white)}

.project-list{left:817px;top:102px;width:303px}
.project{height:78px;border-bottom:1.5px solid var(--green);padding-top:4px}
.project h3{font-size:16.5px;font-weight:500;color:var(--text);white-space:nowrap;line-height:1.15}
.project p{font-size:14px;line-height:1.3;color:var(--muted)}

.brand{left:979px;top:624px;display:flex;align-items:center;gap:7px}
.brand .dot{width:24px;height:24px;border-radius:50%;border:2.5px solid var(--green)}
.brand .word{font-family:"Signika",sans-serif;font-size:17px;font-weight:600;color:var(--green);letter-spacing:.6px}
</style>
</head>
<body>
<div class="slide">

  <div class="abs profile-panel"></div>
  <div class="abs stage-backdrop" role="img" aria-label="Dimmed photo of a conference audience facing a speaker"></div>
  <div class="abs portrait" role="img" aria-label="Photo of the founder speaking at a lectern in front of a presentation screen"></div>

  <div class="abs divider"></div>
  <div class="abs icon-pill">
    <svg style="top:12px" viewBox="0 0 24 24" fill="none" stroke="#fff" stroke-width="1.6"><path d="M12 22s7-7.5 7-13a7 7 0 0 0-14 0c0 5.5 7 13 7 13z"/><circle cx="12" cy="9" r="2.6"/></svg>
    <svg style="top:46px" viewBox="0 0 24 24" fill="none" stroke="#fff" stroke-width="1.6"><rect x="3" y="6" width="18" height="12" rx="1"/><path d="M3 7l9 6 9-6"/></svg>
    <svg style="top:69px" viewBox="0 0 24 24" fill="none" stroke="#fff" stroke-width="1.6"><path d="M5 19c-1-1-1-3 0-4l2-2 3 3-2 2c3 0 8-5 8-8l-2 2-3-3 2-2c1-1 3-1 4 0 3 3-9 15-12 12z"/></svg>
    <svg style="top:93px" viewBox="0 0 24 24" fill="none" stroke="#fff" stroke-width="1.6"><circle cx="12" cy="12" r="9"/><ellipse cx="12" cy="12" rx="4" ry="9"/><path d="M3 12h18M5 7h14M5 17h14"/></svg>
  </div>

  <h1 class="abs name">Corvin <b>Delastre</b></h1>
  <p class="abs role">FOUNDER &amp; MANAGING DIRECTOR</p>
  <div class="abs contact">
    <p class="addr">Talvora Partners GmbH,<br>Lindauer Weg 14, D-10827, Berlin</p>
    <p class="line">delastre@talvora.partners</p>
    <p class="line">(+49) 151 0000 2847</p>
    <p class="line">talvora-partners.net</p>
  </div>

  <section class="abs honorary">
    <h2 class="col-head">HONORARY</h2>
    <div class="entry" style="top:34px">
      <p class="txt">Member of Normtek<br>consortium</p>
      <p class="date">2019 TO DATE</p>
      <div class="badge navy">Normtek</div>
    </div>
    <div class="entry sep" style="top:87px;padding-top:9px">
      <p class="txt">Mainvale University,<br>Wiesbaden</p>
      <p class="date">2018 TO DATE</p>
      <div class="badge white" style="top:10px">Mainvale</div>
    </div>
    <div class="entry sep" style="top:149px;padding-top:9px">
      <p class="txt">Member of Federal<br>Association of<br>Clean Enterprise</p>
      <p class="date">2014 TO DATE</p>
      <div class="badge white" style="top:10px;font-size:9px">Clean Enterprise</div>
    </div>
  </section>

  <section class="abs speaker">
    <h2 class="col-head">SPEAKER</h2>
    <div class="entry" style="top:34px">
      <p class="txt">FWEC “Energy Transition”<br>Vienna, Austria</p>
      <p class="date">2019</p>
      <div class="badge grey"></div>
    </div>
    <div class="entry sep" style="top:87px;padding-top:9px">
      <p class="txt">HSWB, Guest Lecture,<br>Zero Emission Mobility</p>
      <p class="date">2019</p>
      <div class="badge white" style="top:10px"><span class="seal"></span></div>
    </div>
    <div class="entry sep" style="top:149px;padding-top:9px">
      <p class="txt">Velomesse, “Financing<br>Startups” Friedrichshafen,<br>Germany</p>
      <p class="date">2018</p>
      <div class="badge magenta" style="top:10px;height:43px">Velomesse</div>
    </div>
  </section>

  <nav class="abs crumb">
    <span class="num">07</span>
    <span class="path">SMART MOBILITY &amp; KDR &gt;&gt; <b>TEAM</b> &gt;&gt; <span class="hl">CORVIN DELASTRE</span></span>
  </nav>

  <div class="abs rail"></div>
  <div class="abs projects-band"><span>PROJECTS</span></div>
  <div class="abs timeline-line"></div>
  <div class="node" style="top:108px">Haruka<br>Motors</div>
  <div class="node" style="top:186px">Gazeliane</div>
  <div class="node" style="top:263px">Novaris</div>
  <div class="node" style="top:341px">Rentaro<br>Mobility</div>
  <div class="node empty" style="top:417px"></div>
  <div class="node empty" style="top:497px"></div>

  <div class="abs project-list">
    <article class="project"><h3>2017–20: Haruka Motors, Germany</h3><p>Lorem ipsum dolor sit amet consecteur asdciping elud sempre eusimod nonummy</p></article>
    <article class="project"><h3>2018–20: Gazeliane, France</h3><p>Lorem ipsum dolor sit amet consecteur asdciping elud sempre eusimod nonummy</p></article>
    <article class="project"><h3>2018: Novaris Energy Incubator, Sweden</h3><p>Lorem ipsum dolor sit amet consecteur asdciping elud sempre eusimod nonummy</p></article>
    <article class="project"><h3>2016–18: EU New Mobility Survey, Paris</h3><p>Lorem ipsum dolor sit amet consecteur asdciping elud sempre eusimod nonummy</p></article>
    <article class="project"><h3>2012–15: Citystrom E car Sharing, Berlin</h3><p>Lorem ipsum dolor sit amet consecteur asdciping elud sempre eusimod nonummy</p></article>
    <article class="project"><h3>2008–10: Ridesharing, Berlin</h3><p>Lorem ipsum dolor sit amet consecteur asdciping elud sempre eusimod nonummy</p></article>
  </div>

  <div class="abs brand"><span class="dot"></span><span class="word">TALVORA PARTNERS</span></div>
</div>
</body>
</html>
```